A5 Flyer for Financial Services Business

I am after a re-design of our business flyer to fit in with our new branding style and logo colour scheme. Wanting something with a bit of designer flair that I could not create myself. I have included the flyer which I created which lacks style so dazzle me.

I want to use the same content.

Text for main body of flyer is

Are you a small business owner, tradie or TRPQ Service Provider struggling to stay on top of your bookkeeping and compliance obligations? If so we would love to help you get back on track and take control of your business finances so that you can make informed business decisions and focus on what you do best.

We have over 20 years industry experience and, as a small business ourselves, we are able to offer our clients a personal bookkeeping solution tailored to meet the needs of your business.

Accounts Payable | Accounts Receivable
Customer Invoicing
Bank and Credit Card Reconciliations
Payroll | Superannuation | Payroll Tax
Business Activity | Instalment Activity Statements
Regular Financial Reports
Vantly and Brimfolk Set-Up and Training

```html
<!DOCTYPE html>
<html lang="en">
<head>
<meta charset="utf-8">
<title>Even Keel Financial Services – Bookkeeping Flyer</title>
<link rel="stylesheet" href="https://fonts.googleapis.com/css2?family=Poppins:wght@300;500;600;700;800&family=Montserrat:wght@400;600;700&display=swap">
<style>
  :root{
    --navy:#0b3550;
    --navy-deep:#082a40;
    --teal:#0f8a8f;
    --teal-mid:#137a83;
    --teal-light:#1fa9ae;
    --heading:#0d4a6b;
    --ink:#1f2a33;
    --white:#ffffff;
    --silver:#8c959c;
    --badge-border:#b9c2c8;
    --badge-fill:#e4eaed;
    --star:#f2c14e;
  }
  html,body{margin:0;padding:0;}
  body{width:1200px;height:2230px;overflow:hidden;background:var(--white);font-family:'Montserrat',sans-serif;color:var(--ink);}
  .flyer{position:relative;width:1200px;height:2230px;overflow:hidden;background:var(--white);}
  .shapes{position:absolute;left:0;top:0;}

  .brand{position:absolute;left:64px;top:150px;width:520px;text-align:center;}
  .brand-mark{width:64px;height:64px;margin:0 auto 26px;background:var(--teal);}
  .brand-name{font-family:'Poppins',sans-serif;font-weight:300;font-size:50px;letter-spacing:1px;color:var(--teal);line-height:1;}
  .brand-tag{font-family:'Poppins',sans-serif;font-weight:300;font-size:24px;letter-spacing:12px;color:var(--silver);margin-top:10px;}

  .headline{position:absolute;left:64px;top:410px;margin:0;font-family:'Poppins',sans-serif;font-weight:800;font-size:55px;line-height:1.12;color:var(--white);text-transform:uppercase;letter-spacing:.5px;}

  .intro{position:absolute;left:64px;top:722px;width:715px;}
  .intro-question{margin:0;font-family:'Poppins',sans-serif;font-weight:700;font-size:32px;line-height:1.3;color:var(--heading);letter-spacing:-.3px;}
  .intro-body{margin:34px 0 0 4px;font-size:28px;line-height:1.32;color:var(--ink);letter-spacing:-.3px;}

  .experience-content{position:absolute;left:815px;top:628px;width:320px;color:var(--white);}
  .stars{text-align:center;color:var(--star);font-size:38px;letter-spacing:6px;line-height:1;}
  .over{margin-top:20px;text-align:center;font-family:'Poppins',sans-serif;font-weight:500;font-size:31px;letter-spacing:3px;}
  .years{display:flex;align-items:center;justify-content:center;margin-top:4px;}
  .years-num{font-family:'Poppins',sans-serif;font-weight:700;font-size:128px;line-height:.9;color:var(--teal-light);letter-spacing:-6px;margin-right:8px;}
  .years-text{display:flex;flex-direction:column;line-height:1;}
  .years-word{font-family:'Poppins',sans-serif;font-weight:700;font-size:50px;}
  .years-industry{font-family:'Poppins',sans-serif;font-weight:500;font-size:25px;letter-spacing:5px;margin-top:4px;}
  .years-exp{font-family:'Poppins',sans-serif;font-weight:700;font-size:24px;background:var(--teal-light);padding:3px 5px;margin-top:6px;letter-spacing:1px;}
  .experience-note{margin:24px 0 0;font-size:22px;line-height:1.3;}
  .experience-note strong{font-weight:700;}

  .services{position:absolute;left:0;top:1147px;width:1200px;height:714px;background:linear-gradient(180deg,var(--teal-mid) 0%,var(--teal) 60%,#0c7278 100%);}
  .services-divider{position:absolute;left:583px;top:1180px;width:2px;height:640px;background:rgba(255,255,255,.25);}
  .service{position:absolute;display:flex;align-items:center;transform:translateY(-50%);font-family:'Poppins',sans-serif;font-weight:600;font-size:32px;line-height:1.15;color:var(--white);}
  .service svg{flex:0 0 auto;margin-right:18px;}
  .col-left{left:68px;}
  .col-right{left:640px;}

  .contact-tab{position:absolute;left:0;top:1900px;width:455px;height:62px;background:var(--navy);border-radius:0 8px 8px 0;box-shadow:0 4px 8px rgba(0,0,0,.25);font-family:'Poppins',sans-serif;font-weight:700;font-size:32px;color:var(--white);line-height:62px;padding-left:72px;box-sizing:border-box;letter-spacing:.5px;}
  .contact-line{position:absolute;left:64px;display:flex;align-items:center;color:var(--ink);}
  .contact-line svg{margin-right:14px;}
  .phone{top:1995px;font-family:'Poppins',sans-serif;font-weight:700;font-size:50px;}
  .email{top:2080px;font-size:25px;font-weight:600;}
  .web{top:2130px;font-size:25px;font-weight:600;}
  .badges{position:absolute;left:688px;top:1950px;display:flex;gap:10px;}
  .badge{width:140px;height:150px;border:2px solid var(--badge-border);border-radius:8px;display:flex;align-items:center;justify-content:center;background:var(--white);box-sizing:border-box;}
  .badge-shape{width:104px;height:112px;border-radius:6px;background:var(--badge-fill);}
</style>
</head>
<body>
<div class="flyer">
  <svg class="shapes" width="1200" height="1147" viewBox="0 0 1200 1147" aria-hidden="true">
    <defs>
      <linearGradient id="bandGrad" x1="0" y1="0" x2="1" y2="0">
        <stop offset="0" stop-color="#0b3550"/>
        <stop offset=".55" stop-color="#0e5d6e"/>
        <stop offset="1" stop-color="#13959a"/>
      </linearGradient>
      <linearGradient id="triGrad" x1="0" y1="0" x2="0" y2="1">
        <stop offset="0" stop-color="#13959a"/>
        <stop offset="1" stop-color="#0b3550"/>
      </linearGradient>
      <linearGradient id="photoGrad" x1="0" y1="0" x2="1" y2="1">
        <stop offset="0" stop-color="#dfe3e6"/>
        <stop offset=".5" stop-color="#f2f1ef"/>
        <stop offset="1" stop-color="#c9cdd1"/>
      </linearGradient>
    </defs>
    <polygon points="500,0 760,0 622,262" fill="url(#triGrad)"/>
    <polygon points="600,305 628,292 700,470 660,420" fill="#a7aeb4"/>
    <polygon points="0,365 625,365 772,666 0,666" fill="url(#bandGrad)"/>
    <g role="img" aria-label="Photo of a bookkeeper working at a desk with a keyboard, papers and a red mug">
      <polygon points="760,0 1200,0 1200,666 790,666 610,300" fill="url(#photoGrad)"/>
    </g>
    <polygon points="974,553 1165,640 1165,1147 783,1147 783,640" fill="#0f8a8f"/>
    <polygon points="974,575 1148,655 1148,1147 800,1147 800,655" fill="#0b3550"/>
  </svg>

  <div class="brand">
    <div class="brand-mark"></div>
    <div class="brand-name">EVEN KEEL</div>
    <div class="brand-tag">Financial Services</div>
  </div>

  <h1 class="headline">Bookkeeping<br>Tailored to your<br>business needs</h1>

  <section class="intro">
    <p class="intro-question">Are you a small business owner, tradie or TRPQ Service Provider struggling to stay on top of your bookkeeping and compliance obligations?</p>
    <p class="intro-body">If so we would love to help you get back on track and take control of your business finances so that you can make informed business decisions and focus on what you do best.</p>
  </section>

  <div class="experience-content">
    <div class="stars">★★★</div>
    <div class="over">WE HAVE OVER</div>
    <div class="years">
      <span class="years-num">20</span>
      <span class="years-text">
        <span class="years-word">YEARS</span>
        <span class="years-industry">INDUSTRY</span>
        <span class="years-exp">EXPERIENCE</span>
      </span>
    </div>
    <p class="experience-note">And, as a small business ourselves, we are able to offer our clients a <strong>personal bookkeeping solution</strong> tailored to meet the needs of your business.</p>
  </div>

  <section class="services"></section>
  <div class="services-divider"></div>

  <div class="service col-left" style="top:1228px"><svg width="64" height="64" viewBox="0 0 64 64"><circle cx="32" cy="32" r="30" fill="#fff"/><circle cx="32" cy="32" r="25" fill="none" stroke="#0b3550" stroke-width="1.5" stroke-dasharray="3 3"/><rect x="22" y="19" width="20" height="26" rx="2" fill="none" stroke="#0b3550" stroke-width="2"/><path d="M26 27h12M26 32h12M26 37h8" stroke="#0b3550" stroke-width="2"/></svg>Accounts Payable</div>
  <div class="service col-left" style="top:1342px"><svg width="64" height="64" viewBox="0 0 64 64"><circle cx="32" cy="32" r="30" fill="#fff"/><circle cx="32" cy="32" r="25" fill="none" stroke="#0b3550" stroke-width="1.5" stroke-dasharray="3 3"/><rect x="22" y="19" width="20" height="26" rx="2" fill="none" stroke="#0b3550" stroke-width="2"/><path d="M26 27h12M26 32h12M26 37h8" stroke="#0b3550" stroke-width="2"/></svg>Accounts Receivable</div>
  <div class="service col-left" style="top:1450px"><svg width="64" height="64" viewBox="0 0 64 64"><circle cx="32" cy="32" r="30" fill="#fff"/><circle cx="32" cy="32" r="25" fill="none" stroke="#0b3550" stroke-width="1.5" stroke-dasharray="3 3"/><rect x="22" y="19" width="20" height="26" rx="2" fill="none" stroke="#0b3550" stroke-width="2"/><path d="M26 27h12M26 32h12M26 37h8" stroke="#0b3550" stroke-width="2"/></svg>Customer Invoicing</div>
  <div class="service col-left" style="top:1569px"><svg width="64" height="64" viewBox="0 0 64 64"><circle cx="32" cy="32" r="30" fill="#fff"/><circle cx="32" cy="32" r="25" fill="none" stroke="#0b3550" stroke-width="1.5" stroke-dasharray="3 3"/><rect x="18" y="23" width="28" height="18" rx="2" fill="none" stroke="#0b3550" stroke-width="2"/><path d="M18 29h28" stroke="#0b3550" stroke-width="3"/></svg>Bank and Credit Card<br>Reconciliations</div>
  <div class="service col-left" style="top:1672px"><svg width="64" height="64" viewBox="0 0 64 64"><circle cx="32" cy="32" r="30" fill="#fff"/><circle cx="32" cy="32" r="25" fill="none" stroke="#0b3550" stroke-width="1.5" stroke-dasharray="3 3"/><circle cx="32" cy="33" r="11" fill="none" stroke="#0b3550" stroke-width="2"/><path d="M32 26v14M28 30h6M30 36h6" stroke="#0b3550" stroke-width="2"/></svg>Payroll</div>
  <div class="service col-left" style="top:1782px"><svg width="64" height="64" viewBox="0 0 64 64"><circle cx="32" cy="32" r="30" fill="#fff"/><circle cx="32" cy="32" r="25" fill="none" stroke="#0b3550" stroke-width="1.5" stroke-dasharray="3 3"/><path d="M21 42h22M24 42V32M32 42V26M40 42V20" stroke="#0b3550" stroke-width="3"/></svg>Superannuation</div>

  <div class="service col-right" style="top:1226px"><svg width="64" height="64" viewBox="0 0 64 64"><circle cx="32" cy="32" r="30" fill="#fff"/><circle cx="32" cy="32" r="25" fill="none" stroke="#0b3550" stroke-width="1.5" stroke-dasharray="3 3"/><rect x="22" y="19" width="20" height="26" rx="2" fill="none" stroke="#0b3550" stroke-width="2"/><path d="M26 27h12M26 32h12M26 37h8" stroke="#0b3550" stroke-width="2"/></svg>Payroll Tax</div>
  <div class="service col-right" style="top:1338px"><svg width="64" height="64" viewBox="0 0 64 64"><circle cx="32" cy="32" r="30" fill="#fff"/><circle cx="32" cy="32" r="25" fill="none" stroke="#0b3550" stroke-width="1.5" stroke-dasharray="3 3"/><rect x="19" y="25" width="26" height="18" rx="2" fill="none" stroke="#0b3550" stroke-width="2"/><path d="M27 25v-4h10v4" fill="none" stroke="#0b3550" stroke-width="2"/></svg>Business Activity</div>
  <div class="service col-right" style="top:1450px"><svg width="64" height="64" viewBox="0 0 64 64"><circle cx="32" cy="32" r="30" fill="#fff"/><circle cx="32" cy="32" r="25" fill="none" stroke="#0b3550" stroke-width="1.5" stroke-dasharray="3 3"/><path d="M21 42h22M25 42V34M32 42V28M39 42V23" stroke="#0b3550" stroke-width="3"/></svg>Regular Financial Reports</div>
  <div class="service col-right" style="top:1565px"><svg width="64" height="64" viewBox="0 0 64 64"><circle cx="32" cy="32" r="30" fill="#fff"/><circle cx="32" cy="32" r="25" fill="none" stroke="#0b3550" stroke-width="1.5" stroke-dasharray="3 3"/><rect x="22" y="19" width="20" height="26" rx="2" fill="none" stroke="#0b3550" stroke-width="2"/><path d="M26 27h12M26 32h12M26 37h8" stroke="#0b3550" stroke-width="2"/></svg>Instalment Activity<br>Statements</div>
  <div class="service col-right" style="top:1689px"><svg width="64" height="64" viewBox="0 0 64 64"><circle cx="32" cy="32" r="30" fill="#fff"/><circle cx="32" cy="32" r="25" fill="none" stroke="#0b3550" stroke-width="1.5" stroke-dasharray="3 3"/><rect x="18" y="21" width="28" height="18" rx="2" fill="none" stroke="#0b3550" stroke-width="2"/><path d="M26 45h12M32 39v6" stroke="#0b3550" stroke-width="2"/></svg>Vantly and Brimfolk<br>Set-Up and Training</div>

  <div class="contact-tab">CONTACT US TODAY</div>
  <div class="contact-line phone"><svg width="36" height="36" viewBox="0 0 24 24"><path d="M6.6 10.8a15 15 0 0 0 6.6 6.6l2.2-2.2c.3-.3.7-.4 1-.2 1.1.4 2.3.6 3.6.6.6 0 1 .4 1 1V20c0 .6-.4 1-1 1A17 17 0 0 1 3 4c0-.6.4-1 1-1h3.5c.6 0 1 .4 1 1 0 1.3.2 2.5.6 3.6.1.3 0 .7-.2 1z" fill="#0f8a8f"/></svg>0400 512 738</div>
  <div class="contact-line email"><svg width="28" height="22" viewBox="0 0 28 22"><rect x="1" y="1" width="26" height="20" rx="2" fill="#0b3550"/><path d="M2 3l12 9 12-9" fill="none" stroke="#fff" stroke-width="2"/></svg>hello@evenkeelfinancial.com.au</div>
  <div class="contact-line web"><svg width="28" height="28" viewBox="0 0 28 28"><circle cx="14" cy="14" r="12" fill="#0f8a8f"/><path d="M2 14h24M14 2c-5 6-5 18 0 24M14 2c5 6 5 18 0 24" fill="none" stroke="#fff" stroke-width="1.5"/></svg>www.evenkeelfinancial.com.au</div>

  <div class="badges">
    <div class="badge" role="img" aria-label="Tax registration badge"><div class="badge-shape"></div></div>
    <div class="badge" role="img" aria-label="Accounting software certification badge"><div class="badge-shape"></div></div>
    <div class="badge" role="img" aria-label="Accounting software advisor badge"><div class="badge-shape"></div></div>
  </div>
</div>
</body>
</html>
```